Business Card for Polygraph business in Africa

Business Card . Polygraph Examiner based in Tanzania, East Africa.
Business Card will be used to disseminate contact information to potential clients.
It should convey that I am a professional specifically in the polygraph field and perform my work with integrity.

I have attached the business card that I'm currently using, which I threw together myself initially. It's not professional enough.

Target Market(s)

Banks, Accounting Firms, Government Ministries, Gas, Oil, & Gemstone Mining Concerns, Wildlife Conservation NGOs, International companies located in East Africa.

Industry/Entity Type

Business

Contact Information for Business Card

Veritrace Kilonga
Miriam Holloway
PO Box 48317
Arusha, Tanzania
+255 612 839 274
miriamholloway@postvale.example

Colors
00a990
f37122
faa54b

Requirements
Must have
• - Veritrace Kilonga (with the word "Polygraph" being more prominent than the word "Tanzania")
• - Forensic Examinations
• - Employment Screening
• - Should contain a logo of the Continental Truthline Society (of which I'm a member)
• - I would like an accent design (such as the polygraph "squiggles" of a cardio tracing or such as that)
• - My contact information (less prominent, but large enough to read legibly). I would also consider putting the contact information on the second side of the card.
Nice to have
• My color suggestions are changeable.
Should not have
• Anything "cutesy" or "cartoonish"

```html
<!DOCTYPE html>
<html lang="en">
<head>
<meta charset="utf-8">
<title>Veritrace Kilonga – Business Card</title>
<link rel="stylesheet" href="https://fonts.googleapis.com/css2?family=Roboto:wght@400;500;700;900&family=Roboto+Condensed:wght@700&display=swap">
<style>
  :root {
    --stage: #ece9e4;
    --card: #ffffff;
    --brand-blue: #1a4ea0;
    --brand-blue-deep: #143f86;
    --ink-grey: #5a5f66;
    --rule-grey: #8a8f96;
    --badge-fill: #dfe4ef;
    --on-blue: #ffffff;
  }
  * { box-sizing: border-box; margin: 0; padding: 0; }
  html, body {
    width: 1200px; height: 900px; overflow: hidden;
    background: var(--stage);
    font-family: "Roboto", Arial, sans-serif;
  }
  .sheet {
    width: 1200px; height: 900px;
    display: flex; flex-direction: column; align-items: center; justify-content: center;
    gap: 56px;
  }
  .card {
    position: relative;
    width: 640px; height: 366px;
    background: var(--card);
    border-radius: 22px;
    overflow: hidden;
    box-shadow: 0 10px 28px rgba(0,0,0,0.18);
  }

  /* front */
  .front-identity {
    position: absolute; left: 70px; top: 110px;
  }
  .wordmark-main {
    font-weight: 700; font-size: 40px; line-height: 1;
    color: var(--brand-blue); letter-spacing: -0.5px;
  }
  .wordmark-sub {
    font-weight: 700; font-size: 19px; line-height: 1;
    color: var(--brand-blue); letter-spacing: 6px;
    border-top: 2px solid var(--rule-grey);
    margin-top: 6px; padding-top: 5px;
    padding-left: 2px;
  }
  .services {
    margin-top: 12px;
    font-size: 16px; line-height: 1.35; color: var(--ink-grey);
  }

  /* back */
  .back-band {
    position: absolute; inset: 0; width: 100%; height: 100%;
  }
  .member-badge {
    position: absolute; left: 34px; top: 26px;
    width: 62px; height: 62px; border-radius: 50%;
    background: var(--badge-fill);
    border: 3px solid var(--brand-blue);
  }
  .back-identity {
    position: absolute; right: 40px; top: 92px;
    display: flex; align-items: center; gap: 14px;
  }
  .back-identity .dot {
    width: 46px; height: 46px; border-radius: 50%;
    border: 3px solid var(--ink-grey);
  }
  .back-identity .wordmark-main { font-size: 42px; }
  .back-identity .wordmark-sub { font-size: 20px; letter-spacing: 7px; }

  .contact {
    position: absolute; right: 40px; bottom: 26px;
    text-align: right; color: var(--on-blue);
    font-size: 16px; line-height: 1.4;
  }
  .contact .person {
    font-family: "Roboto Condensed", "Roboto", sans-serif;
    font-weight: 700; font-size: 24px; line-height: 1.1; letter-spacing: 0.5px;
    text-transform: uppercase;
  }
  .contact .firm {
    font-family: "Roboto Condensed", "Roboto", sans-serif;
    font-weight: 700; font-size: 17px; text-transform: uppercase; letter-spacing: 0.5px;
    margin-bottom: 2px;
  }
  .contact .line { display: flex; justify-content: flex-end; align-items: center; gap: 8px; }
  .contact .icon { width: 15px; height: 15px; flex: none; }
  .contact .line.no-icon { padding-right: 23px; }
</style>
</head>
<body>
<main class="sheet">

  <section class="card card-front" aria-label="Card front">
    <div class="front-identity">
      <div class="wordmark-main">Veritrace</div>
      <div class="wordmark-sub">Kilonga</div>
      <p class="services">Forensic Examinations<br>Employment Screening</p>
    </div>
  </section>

  <section class="card card-back" aria-label="Card back">
    <svg class="back-band" viewBox="0 0 640 366" preserveAspectRatio="none" aria-hidden="true">
      <polygon points="0,150 250,150 330,210 640,210 640,366 0,366" fill="var(--brand-blue)"/>
      <polyline points="0,162 245,162 325,222 640,222" fill="none" stroke="var(--on-blue)" stroke-width="3"/>
    </svg>

    <div class="member-badge" role="img" aria-label="Continental Truthline Society member badge"></div>

    <div class="back-identity">
      <span class="dot" aria-hidden="true"></span>
      <div>
        <div class="wordmark-main">Veritrace</div>
        <div class="wordmark-sub">Kilonga</div>
      </div>
    </div>

    <address class="contact">
      <div class="person">Miriam Holloway</div>
      <div class="firm">Veritrace Kilonga</div>
      <div class="line">+255 612 839 274
        <svg class="icon" viewBox="0 0 24 24" aria-hidden="true"><path fill="currentColor" d="M6.6 10.8a15.1 15.1 0 0 0 6.6 6.6l2.2-2.2c.3-.3.7-.4 1-.2 1.1.4 2.3.6 3.6.6.6 0 1 .4 1 1V20c0 .6-.4 1-1 1A17 17 0 0 1 3 4c0-.6.4-1 1-1h3.5c.6 0 1 .4 1 1 0 1.3.2 2.5.6 3.6.1.3 0 .7-.2 1z"/></svg>
      </div>
      <div class="line">miriamholloway@postvale.example
        <svg class="icon" viewBox="0 0 24 24" aria-hidden="true"><path fill="currentColor" d="M3 5h18c.6 0 1 .4 1 1v12c0 .6-.4 1-1 1H3c-.6 0-1-.4-1-1V6c0-.6.4-1 1-1zm9 7.5L4 7.6V8l8 5 8-5v-.4z"/></svg>
      </div>
      <div class="line no-icon">PO Box 48317, Arusha, Tanzania</div>
    </address>
  </section>

</main>
</body>
</html>
```